Business Cards Design for the electrical wholesaler: clean bold dynamic :)

We need a business card design that would follow our latest brand guidelines. As an electrical wholesaler we want to bring a fresh look and feel into the industry. The design should be clean bold and dynamic. It should come alive with the renewed energy of our green colour. Our grey colour should keep things balanced and complement the notion of maturity and responsibility. We employ Lato as a corporate font however are not bound by this font and we’re open to interpretation here.

Target Market(s)

Electrical contractors

Industry/Entity Type

Business

Contact Information for Business Card

Logo
Name & Surname: Halyna Dorosh
Job Title: Director of Marketing
Email: halya.dorosh@quillmail.example
Cell phone: 780.555.0147
Address: 20517 - 87 Ave. Edmonton, AB, Canada. T6K 4N8
Business Phone: 780.555.0184
Website: www.brovix.example

Font styles to use
Other font styles liked:
• Lato

Requirements
Must have
• Logo & website
Nice to have
• Brand elements - some of them you may find in the attached Brand Guidelines (e.g. three lines on the background signifying "W")

```html
<!DOCTYPE html>
<html lang="en">
<head>
<meta charset="utf-8">
<title>Brovix Electrical Wholesalers – Business Card</title>
<link rel="stylesheet" href="https://fonts.googleapis.com/css2?family=Exo+2:wght@600&family=Roboto:wght@400;500&display=swap">
<style>
  :root {
    --page: #3a3a3a;
    --card: #1f1f20;
    --card-edge: #2a2a2b;
    --green: #7dc71f;
    --grey-light: #bdbdbd;
    --emboss: #343436;
    --white: #f2f2f2;
  }
  * { margin: 0; padding: 0; box-sizing: border-box; }
  html, body { width: 799px; height: 1200px; overflow: hidden; }
  body {
    background: var(--page);
    font-family: "Roboto", sans-serif;
    position: relative;
  }
  .card {
    position: absolute;
    left: 80px;
    width: 640px;
    height: 370px;
    border-radius: 26px;
    background: var(--card);
    border: 1px solid var(--card-edge);
    overflow: hidden;
  }
  .card--front { top: 110px; }
  .card--back { top: 690px; }

  .brand {
    position: absolute;
    display: flex;
    align-items: center;
    gap: 14px;
  }
  .brand__dot { border-radius: 50%; flex: none; }
  .brand__name {
    font-family: "Roboto", sans-serif;
    font-weight: 500;
    line-height: 1;
    letter-spacing: 1px;
  }
  .brand__tagline {
    position: absolute;
    font-family: "Roboto", sans-serif;
    font-weight: 500;
    text-transform: uppercase;
    letter-spacing: 2px;
  }

  /* front */
  .card--front .brand { left: 150px; top: 135px; }
  .card--front .brand__dot { width: 70px; height: 70px; background: var(--emboss); }
  .card--front .brand__name { font-size: 86px; color: var(--emboss); }
  .card--front .brand__tagline { left: 236px; top: 232px; font-size: 15px; color: var(--emboss); }

  /* back */
  .accent-arc {
    position: absolute;
    left: -38px; top: 18px;
    width: 64px; height: 64px;
    border-radius: 50%;
    background: var(--green);
  }
  .person { position: absolute; left: 44px; top: 30px; }
  .person__name {
    font-family: "Exo 2", sans-serif;
    font-weight: 600;
    font-size: 27px;
    color: var(--green);
    line-height: 1.1;
  }
  .person__title { font-size: 15px; color: var(--white); margin-top: 2px; }

  .card--back .brand { left: 330px; top: 112px; }
  .card--back .brand__dot { width: 52px; height: 52px; background: var(--green); }
  .card--back .brand__name { font-size: 62px; color: var(--grey-light); }
  .card--back .brand__tagline { left: 397px; top: 182px; font-size: 11px; color: var(--green); }

  .decor {
    position: absolute;
    right: -110px; bottom: -215px;
    width: 360px; height: 360px;
    border-radius: 50%;
    background: linear-gradient(135deg, #2b2b2c 0%, #6a6a6a 55%, #d0d0d0 100%);
  }

  .contact {
    position: absolute;
    left: 40px; top: 214px;
    font-size: 14px;
    color: var(--white);
    line-height: 1.5;
    list-style: none;
  }
  .contact li { display: flex; align-items: center; gap: 8px; }
  .contact svg { width: 13px; height: 13px; flex: none; }
</style>
</head>
<body>

  <section class="card card--front" aria-label="Business card front">
    <div class="brand">
      <span class="brand__dot"></span>
      <span class="brand__name">brovix</span>
    </div>
    <span class="brand__tagline">Electrical Wholesalers</span>
  </section>

  <section class="card card--back" aria-label="Business card back">
    <span class="accent-arc"></span>
    <div class="person">
      <p class="person__name">Halyna Dorosh</p>
      <p class="person__title">Director of Marketing</p>
    </div>

    <div class="brand">
      <span class="brand__dot"></span>
      <span class="brand__name">brovix</span>
    </div>
    <span class="brand__tagline">Electrical Wholesalers</span>

    <span class="decor"></span>

    <ul class="contact">
      <li>20517 - 87 Ave. Edmonton,</li>
      <li>AB, Canada. T6K 4N8</li>
      <li>
        <svg viewBox="0 0 14 14"><circle cx="7" cy="7" r="7" fill="#7dc71f"/><path d="M4.5 3.5l1.4 1.6-.7 1c.5 1 1.2 1.7 2.2 2.2l1-.7 1.6 1.4-.9 1.2C6.4 10 4 7.6 3.3 4.4z" fill="#1f1f20"/></svg>
        780.555.0184
      </li>
      <li>
        <svg viewBox="0 0 14 14"><circle cx="7" cy="7" r="7" fill="#7dc71f"/><rect x="5" y="3" width="4" height="8" rx="0.8" fill="none" stroke="#1f1f20" stroke-width="1"/><circle cx="7" cy="9.6" r=".5" fill="#1f1f20"/></svg>
        780.555.0147
      </li>
      <li>
        <svg viewBox="0 0 14 14"><circle cx="7" cy="7" r="7" fill="#7dc71f"/><rect x="3.5" y="4.5" width="7" height="5" fill="none" stroke="#1f1f20" stroke-width="1"/><path d="M3.5 4.5L7 7.3l3.5-2.8" fill="none" stroke="#1f1f20" stroke-width="1"/></svg>
        halya.dorosh@quillmail.example
      </li>
      <li>
        <svg viewBox="0 0 14 14"><circle cx="7" cy="7" r="7" fill="#7dc71f"/><circle cx="7" cy="7" r="3.6" fill="none" stroke="#1f1f20" stroke-width="1"/><path d="M3.4 7h7.2M7 3.4c-1.6 2.2-1.6 5 0 7.2M7 3.4c1.6 2.2 1.6 5 0 7.2" fill="none" stroke="#1f1f20" stroke-width=".8"/></svg>
        www.brovix.example
      </li>
    </ul>
  </section>

</body>
</html>
```